New Webpage for High Class Expert Witness Services Company

We are looking for a minimalist design for a webpage that just has our logo and an entry form offer to connect with one of our Liaisons.
The entry form should just ask for Name, Email, Contact Info and Description of Project.

Company Name is: The Marlowe Crest Advisory Services

Number of Pages Required

1 page

```html
<!DOCTYPE html>
<html lang="en">
<head>
<meta charset="UTF-8">
<title>The Marlowe Crest Advisory Services — Connect with a Liaison</title>
<link href="https://fonts.googleapis.com/css2?family=Poppins:wght@400;500;600&display=swap" rel="stylesheet">
<style>
  :root {
    --bg-deep: #070707;
    --bg-mid: #141414;
    --panel: rgba(40, 40, 40, 0.55);
    --field: #ffffff;
    --placeholder: #7a7a7a;
    --text: #ffffff;
    --brand: #d9d9d9;
    --button: #161616;
  }
  * { box-sizing: border-box; margin: 0; padding: 0; }
  html, body { width: 1200px; height: 844px; overflow: hidden; }
  body {
    position: relative;
    background: var(--bg-deep);
    font-family: "Poppins", sans-serif;
    color: var(--text);
  }
  .backdrop {
    position: absolute; inset: 0;
    background:
      radial-gradient(ellipse 260px 200px at 1020px 420px, #1c1c1c 0%, transparent 100%),
      radial-gradient(ellipse 320px 260px at 230px 620px, #1a1a1a 0%, transparent 100%),
      radial-gradient(ellipse 300px 140px at 680px 740px, #161616 0%, transparent 100%),
      linear-gradient(180deg, var(--bg-deep) 0%, var(--bg-mid) 70%, #101010 100%);
  }
  .brand {
    position: absolute; left: 0; right: 0; top: 112px;
    text-align: center;
    color: var(--brand);
    font-weight: 500;
    letter-spacing: 0.08em;
  }
  .brand-name { font-size: 22px; line-height: 30px; text-transform: uppercase; }
  .brand-tagline { font-size: 10px; line-height: 18px; letter-spacing: 0.28em; margin-top: 8px; text-transform: uppercase; }
  .contact-panel {
    position: absolute; left: 395px; top: 230px;
    width: 430px; height: 438px;
    background: var(--panel);
  }
  .contact-form { position: absolute; left: 26.5px; top: 0; width: 377px; }
  .field-label {
    position: absolute; left: 0;
    font-size: 12.75px; font-weight: 600; line-height: 16px;
    text-transform: uppercase;
  }
  .field-input {
    position: absolute; left: 0; width: 377px; height: 42px;
    background: var(--field); border: 0;
    padding-left: 21px;
    font-family: "Poppins", sans-serif; font-size: 12px; color: #222;
  }
  .field-input::placeholder { color: var(--placeholder); }
  textarea.field-input { height: 101px; resize: none; padding-top: 12px; }
  .submit-button {
    position: absolute; left: 0; top: 381px; width: 377px; height: 42px;
    background: var(--button); border: 0; color: var(--text);
    font-family: "Poppins", sans-serif; font-size: 12px; font-weight: 600;
    text-transform: uppercase;
  }
  .copyright {
    position: absolute; left: 0; right: 0; top: 790px;
    text-align: center; font-size: 15px; font-weight: 600;
  }
</style>
</head>
<body>
  <div class="backdrop" role="img" aria-label="Dark photograph of soldiers, an armoured vehicle and a helicopter in silhouette"></div>

  <header class="brand">
    <div class="brand-name">The Marlowe Crest Advisory Services</div>
    <div class="brand-tagline">Seamless Medical Expert Integration</div>
  </header>

  <section class="contact-panel">
    <form class="contact-form">
      <label class="field-label" style="top:23px" for="name">Name</label>
      <input class="field-input" style="top:44.5px" id="name" type="text" placeholder="Johny Smith">

      <label class="field-label" style="top:98px" for="email">Email</label>
      <input class="field-input" style="top:120px" id="email" type="email" placeholder="Johny@email.com">

      <label class="field-label" style="top:172px" for="contact">Contact Info</label>
      <input class="field-input" style="top:194.5px" id="contact" type="text" placeholder="+081 123456789">

      <label class="field-label" style="top:246.5px" for="project">Description of Project</label>
      <textarea class="field-input" style="top:269px" id="project"></textarea>

      <button class="submit-button" type="submit">Connect with us</button>
    </form>
  </section>

  <footer class="copyright">Copyright 2026 | All Rights Reserved</footer>
</body>
</html>
```